Heron Loan Partners Business Card

We need a business card design for our mortgage servicing company. In addition to servicing the loans of homeowners, we help homeowners with purchasing their homes and any mortgage refinancing. We would like to see designs that use the colors in the logo attached below (gold-ish yellow and navy blue), and any other design you deem fit! The design should communicate a simpler life with smart mortgages provided by Heron.

```html
<!DOCTYPE html>
<html lang="en">
<head>
<meta charset="utf-8">
<title>Heron Loan Partners – Business Card</title>
<link href="https://fonts.googleapis.com/css2?family=Poppins:wght@400;500;600;700&display=swap" rel="stylesheet">
<style>
  :root {
    --navy: #211d4e;
    --gold: #e0b23c;
    --paper: #f7f7f7;
    --paper-shade: #ececec;
    --ink: #211d4e;
    --page: #ffffff;
  }
  * { margin: 0; padding: 0; box-sizing: border-box; }
  html, body {
    width: 734px; height: 1200px; overflow: hidden;
    background: var(--page);
    font-family: "Poppins", sans-serif;
    color: var(--ink);
  }
  .card {
    position: absolute; left: 67px;
    width: 600px; height: 344px;
    overflow: hidden;
    box-shadow: 0 6px 14px rgba(0,0,0,.22);
  }
  .card--front { top: 216px; }
  .card--back { top: 620px; }
  .card__texture {
    position: absolute; inset: 0;
    background: linear-gradient(160deg, var(--paper) 0%, var(--paper-shade) 50%, var(--paper) 100%);
  }

  /* front */
  .front__brand {
    position: absolute; left: 0; right: 0; top: 122px;
    text-align: center;
    font-weight: 700; font-size: 46px; letter-spacing: -0.5px;
    color: var(--gold);
  }
  .front__url-band {
    position: absolute; left: 0; top: 0; width: 600px; height: 344px;
  }
  .front__url {
    position: absolute; left: 145px; width: 320px; top: 289px; height: 27px;
    display: flex; align-items: center; justify-content: center;
    font-size: 15px; letter-spacing: 4px; color: #fff; font-weight: 500;
  }
  .front__url b { color: var(--gold); font-weight: 700; }

  /* back */
  .back__tab {
    position: absolute; left: 0; top: 101px; width: 43px; height: 36px;
    background: var(--gold);
  }
  .back__name {
    position: absolute; left: 54px; top: 99px;
    font-size: 22px; font-weight: 700; line-height: 1; letter-spacing: -.2px;
    color: var(--navy);
  }
  .back__name span { color: var(--gold); }
  .back__company {
    position: absolute; left: 54px; top: 123px;
    font-size: 13.5px; font-weight: 600; color: var(--navy);
  }
  .contact__rail {
    position: absolute; left: 54px; top: 173px; width: 20px; height: 93px;
    border-radius: 10px; background: var(--gold);
  }
  .contact__list { list-style: none; position: absolute; left: 54px; top: 176px; }
  .contact__item {
    display: flex; align-items: center; height: 21.5px;
    font-size: 11.5px; font-weight: 600; color: #222;
  }
  .contact__icon {
    width: 14px; height: 14px; margin: 0 13px 0 3px;
    border-radius: 50%; background: #fff;
    display: flex; align-items: center; justify-content: center;
  }
  .contact__icon svg { width: 9px; height: 9px; fill: var(--navy); }
  .back__brand {
    position: absolute; left: 390px; top: 96px; width: 170px;
    text-align: center;
    font-size: 28px; font-weight: 700; color: var(--gold);
  }
  .back__band { position: absolute; left: 0; top: 0; }
</style>
</head>
<body>

<section class="card card--front" aria-label="Business card front">
  <div class="card__texture" role="img" aria-label="Soft wavy sand texture on white card stock"></div>
  <div class="front__brand">Heron Loan Partners</div>
  <svg class="front__url-band" viewBox="0 0 600 344" aria-hidden="true">
    <polygon points="157,289 466,289 454,316 145,316" fill="var(--navy)"/>
    <polygon points="0,317 117,317 124,313 482,313 475,317 600,317 600,344 0,344" fill="var(--gold)"/>
  </svg>
  <div class="front__url">www.<b>heronloans</b>.com</div>
</section>

<section class="card card--back" aria-label="Business card back">
  <div class="card__texture" role="img" aria-label="Soft wavy sand texture on white card stock"></div>
  <div class="back__tab"></div>
  <h1 class="back__name">HERON <span>WHITLEY</span></h1>
  <p class="back__company">Harborline</p>

  <div class="contact__rail"></div>
  <ul class="contact__list">
    <li class="contact__item">
      <span class="contact__icon"><svg viewBox="0 0 24 24"><path d="M6.6 10.8a15.1 15.1 0 0 0 6.6 6.6l2.2-2.2a1 1 0 0 1 1-.25 11.4 11.4 0 0 0 3.6.57 1 1 0 0 1 1 1V20a1 1 0 0 1-1 1A17 17 0 0 1 3 4a1 1 0 0 1 1-1h3.5a1 1 0 0 1 1 1c0 1.25.2 2.45.57 3.57a1 1 0 0 1-.25 1z"/></svg></span>
      833-555-0142
    </li>
    <li class="contact__item">
      <span class="contact__icon"><svg viewBox="0 0 24 24"><path d="M2 5h20v14H2z M2 5l10 8 10-8" fill="var(--navy)"/><path d="M3 6l9 7 9-7" stroke="#fff" stroke-width="2" fill="none"/></svg></span>
      sales@heronloans.com
    </li>
    <li class="contact__item">
      <span class="contact__icon"><svg viewBox="0 0 24 24"><path d="M12 2a7 7 0 0 0-7 7c0 5 7 13 7 13s7-8 7-13a7 7 0 0 0-7-7zm0 9.5A2.5 2.5 0 1 1 12 6.5a2.5 2.5 0 0 1 0 5z"/></svg></span>
      24 Bayview Court, Suite 210, Brookfield, NJ 07010
    </li>
    <li class="contact__item">
      <span class="contact__icon"><svg viewBox="0 0 24 24"><circle cx="12" cy="12" r="10" fill="none" stroke="var(--navy)" stroke-width="2.4"/><path d="M2 12h20M12 2c3 3 3 17 0 20M12 2c-3 3-3 17 0 20" fill="none" stroke="var(--navy)" stroke-width="2"/></svg></span>
      www.heronloans.com
    </li>
  </ul>

  <div class="back__brand">Heron</div>

  <svg class="back__band" width="600" height="344" viewBox="0 0 600 344" aria-hidden="true">
    <polygon points="332,328 600,328 600,344 320,344" fill="var(--navy)"/>
  </svg>
</section>

</body>
</html>
```